New Business Card Design Project

We require a business card design for Vexalund, a newly established Indian company.
Our focus is on the development, manufacturing, and export of a diverse array of pharmaceutical products on a global scale. The card should convey a professional appearance, as our primary markets are in Africa, China, and Southeast Asian nations.
We envision a two-sided business card, with the reverse side dedicated to a logo set against a solid color or an elegantly designed pattern. The corners should be rounded. We would appreciate seeing both horizontal and vertical design options. We trust the designer to utilize their expertise in creating this design.

The content for the business card is included in the attached Word file.

Target Market(s)

Our primary markets are in Africa, China, and Southeast Asian, Latin America, Maldives, Sri Lanka

Industry/Entity Type

Pharmaceutical Manufacturing and Export

Contact Information for Business Card

Colors

Designer to choose colors to be used in the design.

Requirements
Must have
• The reverse side of the business card features solely the logo along with the tagline, "Care for Every Life."
Should not have
• The logo should not exceed two instances, encompassing both the front and back sides of the card.

```html
<!DOCTYPE html>
<html lang="en">
<head>
<meta charset="utf-8">
<title>Vexalund Business Card</title>
<link href="https://fonts.googleapis.com/css2?family=Montserrat:wght@800&family=Open+Sans:wght@400;600&family=Poppins:wght@400&display=swap" rel="stylesheet">
<style>
  :root {
    --stage: #232323;
    --coral: #ef6351;
    --ink: #222327;
    --sky: #2ea8e0;
    --white: #ffffff;
    --muted: #e8e8ea;
    --ghost: #2b2f36;
  }
  * { margin: 0; padding: 0; box-sizing: border-box; }
  html, body { width: 1200px; height: 711px; overflow: hidden; }
  body {
    background: var(--stage);
    display: flex;
    align-items: center;
    justify-content: center;
    gap: 60px;
  }
  .card {
    position: relative;
    width: 500px;
    height: 286px;
    border-radius: 22px;
    overflow: hidden;
    box-shadow: 0 14px 30px rgba(0,0,0,.55);
  }

  /* Reverse side */
  .card-back {
    background: var(--coral);
    display: flex;
    flex-direction: column;
    align-items: center;
    justify-content: center;
    color: var(--white);
  }
  .brand {
    display: flex;
    align-items: center;
    gap: 12px;
  }
  .brand-dot {
    border-radius: 50%;
    background: currentColor;
  }
  .card-back .brand-dot { width: 30px; height: 30px; }
  .card-back .brand-name {
    font: 800 54px/1 "Montserrat", sans-serif;
    letter-spacing: -0.5px;
  }
  .tagline {
    margin-top: 18px;
    font: 400 13px/1 "Poppins", sans-serif;
    letter-spacing: 0.5px;
  }

  /* Front side */
  .card-front {
    background: var(--ink);
    color: var(--white);
    font-family: "Open Sans", sans-serif;
  }
  .ghost-mark {
    position: absolute;
    right: 30px;
    top: 50px;
    width: 190px;
    height: 190px;
    border-radius: 50%;
    background: var(--ghost);
    opacity: .6;
  }
  .card-front .brand {
    position: absolute;
    left: 30px;
    top: 34px;
    color: var(--sky);
    gap: 9px;
  }
  .card-front .brand-dot { width: 18px; height: 18px; }
  .card-front .brand-name {
    font: 800 32px/1 "Montserrat", sans-serif;
  }
  .address {
    position: absolute;
    left: 32px;
    top: 92px;
    font-size: 12.5px;
    line-height: 1.55;
    color: var(--muted);
  }
  .contacts {
    position: absolute;
    left: 32px;
    bottom: 28px;
    list-style: none;
    font-size: 12.5px;
    color: var(--muted);
  }
  .contacts li {
    display: flex;
    align-items: center;
    gap: 10px;
    height: 22px;
  }
  .contacts svg { width: 14px; height: 14px; flex: none; }
  .person {
    position: absolute;
    right: 34px;
    top: 118px;
    text-align: right;
  }
  .person-name {
    font-size: 22px;
    line-height: 1.1;
    white-space: nowrap;
  }
  .first-name { color: var(--sky); font-weight: 600; }
  .last-name { color: var(--coral); font-weight: 400; }
  .person-role {
    font-size: 12px;
    color: var(--white);
    margin-top: 2px;
  }
  .accent-bar {
    position: absolute;
    right: 0;
    top: 112px;
    width: 16px;
    height: 44px;
    background: var(--sky);
  }
</style>
</head>
<body>

  <section class="card card-back" aria-label="Card reverse">
    <div class="brand">
      <span class="brand-dot"></span>
      <span class="brand-name">Vexalund</span>
    </div>
    <p class="tagline">Care for Every Life.</p>
  </section>

  <section class="card card-front" aria-label="Card front">
    <div class="ghost-mark" aria-hidden="true"></div>

    <div class="brand">
      <span class="brand-dot"></span>
      <span class="brand-name">Vexalund</span>
    </div>

    <p class="address">14, Neelkanth Nagar,<br>Akola, 444001, India</p>

    <ul class="contacts">
      <li>
        <svg viewBox="0 0 14 14" aria-hidden="true"><rect x="3.5" y="1" width="7" height="12" rx="1.2" fill="none" stroke="#ef6351" stroke-width="1.4"/></svg>
        +91 98765 43120
      </li>
      <li>
        <svg viewBox="0 0 14 14" aria-hidden="true"><circle cx="7" cy="7" r="6" fill="none" stroke="#2ea8e0" stroke-width="1.4"/><ellipse cx="7" cy="7" rx="2.6" ry="6" fill="none" stroke="#2ea8e0" stroke-width="1.1"/><line x1="1" y1="7" x2="13" y2="7" stroke="#2ea8e0" stroke-width="1.1"/></svg>
        www.vexalund.com
      </li>
      <li>
        <svg viewBox="0 0 14 14" aria-hidden="true"><rect x="1" y="3" width="12" height="9" rx="1" fill="none" stroke="#ef6351" stroke-width="1.4"/><polyline points="1.5,3.5 7,8 12.5,3.5" fill="none" stroke="#ef6351" stroke-width="1.3"/></svg>
        asalunke@vexalund.com
      </li>
    </ul>

    <div class="person">
      <p class="person-name"><span class="first-name">Arvind</span> <span class="last-name">K. Salunke</span></p>
      <p class="person-role">CEO</p>
    </div>
    <div class="accent-bar"></div>
  </section>

</body>
</html>
```